New Business Card Design for Manufacturing

We are an engineering/manufacturing company that offers Advanced machining/assembly/engineering services, as well as innovative products for the heavy duty engine cooling markets.

We are looking to get a new business card designed that is clean and modern looking, but still fits the wide range of technical/skilled work we do.

- We hope to use this design as the base for other design work in new Presentations, web, and print work.

Industry/Entity Type

Engineering

Contact Information for Business Card

Our preferred color of blue is (RGB) 22/71/159 but can vary slightly from that color. Our content will be our Logo and full company name (Vantrell Forge Works, Inc.), company address, name, job title, phone number with extension, cell number, fax number, website, and email address on the cards.
We'd like the full company name next to the logo, but we are open to other interpretations of that layout.
Preferably, we would like the back side to be clean with just our logo, and the front to contain all of the contact information.

Colors
2f74b4
0355a3
85abd2

Requirements
Must have
• - Logo, company name, needed content - We are open to interpretation beyond that.
• - Standard size business card.
• - Horizontal orientation.
• - Enough space for lengthy names / job titles (for example, a job title could read "Directory of Human Resources" or "V.P. of Governmental Affairs"). We need this to look clean, whether the title be short (CEO) or long (as described above).

```html
<!DOCTYPE html>
<html lang="en">
<head>
<meta charset="utf-8">
<title>Vantrell Forge Works – Business Card</title>
<link href="https://fonts.googleapis.com/css2?family=Lato:wght@400;700&family=Montserrat:wght@500;800&display=swap" rel="stylesheet">
<style>
  :root{
    --brand-blue:#1652a2;
    --brand-blue-deep:#0f4c9e;
    --rule-grey:#9aa1a9;
    --ink:#3a3d42;
    --paper:#ffffff;
    --backdrop:#3a3531;
  }
  *{margin:0;padding:0;box-sizing:border-box}
  html,body{width:1200px;height:930px;overflow:hidden;background:var(--backdrop)}
  .stage{position:relative;width:1200px;height:930px}
  .card{position:absolute;width:560px;height:320px;overflow:hidden;box-shadow:0 6px 18px rgba(0,0,0,.35)}

  /* back side */
  .card--back{left:70px;top:80px;background:var(--brand-blue-deep)}
  .card--back .wordmark{position:absolute;left:0;right:0;top:112px;display:flex;justify-content:center;align-items:center;gap:14px}
  .card--back .wordmark__square{width:40px;height:40px;background:var(--paper)}
  .card--back .wordmark__name{font-family:"Montserrat",sans-serif;font-weight:800;font-size:25px;line-height:1.05;color:var(--paper);letter-spacing:.5px;text-transform:uppercase}
  .card--back .website{position:absolute;left:0;right:0;bottom:38px;text-align:center;font-family:"Lato",sans-serif;font-size:14px;letter-spacing:2px;color:var(--paper)}

  /* front side */
  .card--front{left:570px;top:530px;background:var(--paper)}
  .card--front .wordmark{position:absolute;left:34px;top:40px;display:flex;align-items:center;gap:12px}
  .card--front .wordmark__square{width:34px;height:34px;background:var(--brand-blue)}
  .card--front .wordmark__name{font-family:"Montserrat",sans-serif;font-weight:800;font-size:18px;line-height:1.05;color:var(--brand-blue);text-transform:uppercase}
  .person{position:absolute;left:90px;top:112px}
  .person__name{font-family:"Montserrat",sans-serif;font-weight:500;font-size:28px;color:var(--brand-blue);letter-spacing:.5px;text-transform:uppercase}
  .person__title{font-family:"Lato",sans-serif;font-size:15px;color:var(--ink);margin-top:2px}
  .contacts{position:absolute;left:90px;right:28px;top:170px;display:flex;justify-content:space-between;align-items:flex-end;height:44px;font-family:"Lato",sans-serif;font-size:14px;line-height:1.45;color:var(--ink)}
  .contacts .label{color:var(--brand-blue)}
  .rule{position:absolute;left:0;right:0;top:226px;height:2px;background:var(--rule-grey)}
  .band{position:absolute;left:0;right:0;top:234px;bottom:0;background:var(--brand-blue)}
  .band .website{position:absolute;left:0;right:0;top:32px;text-align:center;font-family:"Lato",sans-serif;font-size:15px;letter-spacing:3px;color:var(--paper);padding-left:90px}
</style>
</head>
<body>
<div class="stage">

  <section class="card card--back" aria-label="Business card, back">
    <div class="wordmark">
      <span class="wordmark__square"></span>
      <span class="wordmark__name">Vantrell Forge<br>Works, Inc.</span>
    </div>
    <p class="website">www.vantrellforge.com</p>
  </section>

  <section class="card card--front" aria-label="Business card, front">
    <div class="wordmark">
      <span class="wordmark__square"></span>
      <span class="wordmark__name">Vantrell Forge<br>Works, Inc.</span>
    </div>

    <div class="person">
      <h1 class="person__name">Dorian Kessler</h1>
      <p class="person__title">Directory of Human Resources</p>
    </div>

    <div class="contacts">
      <div class="contacts__phones">
        <div><span class="label">Phone:</span> 4410- ext</div>
        <div><span class="label">Cell:</span> 555-318-4402</div>
      </div>
      <div class="contacts__office">
        <div><span class="label">fax:</span> (555)318-4403</div>
        <div>d.kessler@vantrellforge.com</div>
      </div>
      <div class="contacts__address">
        <div>2480 Harlow Ave.</div>
        <div>Brookfield, OH 44403</div>
      </div>
    </div>

    <div class="rule"></div>
    <div class="band">
      <p class="website">www.vantrellforge.com</p>
    </div>
  </section>

</div>
</body>
</html>
```